Structural Engineering Business Card

Brookvane Drafting does residential house plans for clients in Central Florida. Would like simple but elegant business card that is appropriate for a house plan engineering company. Prefer black business card with black/white them but open to other shades of blue. I uploaded a sample card that I came across that looked good but please come up with your own creative designs.

Contact Information for Business Card

Name, Title, Phone, Email, Address, website

```html
<!DOCTYPE html>
<html lang="en">
<head>
<meta charset="utf-8">
<title>Brookvane Drafting — Business Card</title>
<link href="https://fonts.googleapis.com/css2?family=Open+Sans:wght@400;700;800&display=swap" rel="stylesheet">
<style>
  :root {
    --stage: #8c8c8f;
    --card-navy: #1a1466;
    --card-navy-deep: #130f52;
    --emboss: #241d7a;
    --ink-light: #ffffff;
    --ink-soft: #d9d8ee;
  }
  * { box-sizing: border-box; margin: 0; padding: 0; }
  html, body {
    width: 1200px; height: 781px; overflow: hidden;
    background: var(--stage);
    font-family: "Open Sans", Arial, sans-serif;
  }
  .sheet {
    width: 1200px; height: 781px;
    display: flex; align-items: center; justify-content: center; gap: 60px;
  }
  .card {
    position: relative;
    width: 500px; height: 286px;
    border-radius: 18px;
    box-shadow: 0 14px 30px rgba(0,0,0,0.35);
    overflow: hidden;
  }
  .card--front { background: var(--card-navy); }
  .card--back { background: var(--card-navy-deep); }

  .contact { position: absolute; left: 34px; top: 30px; color: var(--ink-soft); }
  .contact__name {
    color: var(--ink-light); font-weight: 700; font-size: 14px;
    letter-spacing: 1px; text-transform: uppercase;
  }
  .contact__title { font-size: 10px; margin-bottom: 14px; }
  .contact__address { font-size: 11px; line-height: 1.45; margin-bottom: 8px; }
  .contact__list { list-style: none; font-size: 11px; line-height: 1.55; }
  .contact__list li { display: flex; align-items: center; gap: 6px; }
  .contact__list svg { width: 9px; height: 9px; fill: var(--ink-light); flex: none; }

  .brand {
    position: absolute; right: 30px; bottom: 26px;
    color: var(--ink-light); font-weight: 800; font-size: 26px;
    text-transform: uppercase; letter-spacing: 0.5px; line-height: 1.05;
    text-align: right;
  }
  .brand--emboss {
    right: auto; bottom: auto; left: 50%; top: 50%;
    transform: translate(-50%, -50%);
    color: var(--emboss); font-size: 36px; text-align: center; white-space: nowrap;
  }
</style>
</head>
<body>
<main class="sheet">
  <section class="card card--front" aria-label="Card front">
    <div class="contact">
      <p class="contact__name">Maren Ostlund</p>
      <p class="contact__title">Director</p>
      <p class="contact__address">Harbor Row Planning Office<br>PO Box 4410<br>Lindenfield, FL 32900-1184</p>
      <ul class="contact__list">
        <li><svg viewBox="0 0 10 10"><path d="M2 0.5l2 2-1 1.2c.6 1.3 1.6 2.3 2.9 2.9l1.2-1 2 2-1.2 1.9C4 9.3.7 6 .5 2z"/></svg>(555) 214-3390</li>
        <li><svg viewBox="0 0 10 10"><rect x="1" y="0.5" width="8" height="9" rx="1"/></svg>(555) 214-3391</li>
        <li><svg viewBox="0 0 10 10"><path d="M0 2h10v6H0zM0 2l5 3.5L10 2" stroke="#1a1466" stroke-width="0.8"/></svg>hello@brookvanedrafting.com</li>
        <li><svg viewBox="0 0 10 10"><circle cx="5" cy="5" r="4.5"/></svg>www.brookvanedrafting.com</li>
      </ul>
    </div>
    <p class="brand">Brookvane<br>Drafting</p>
  </section>

  <section class="card card--back" aria-label="Card back">
    <p class="brand brand--emboss">Brookvane Drafting</p>
  </section>
</main>
</body>
</html>
```